Super Greens Label for Supplement Bottle

We want to design a front label for a health supplement bottle. The product is called Meadow Crunch Chews™. This will be a new product so there is no current website for the product. The focus is on supergreens that taste great and deliver support for energy, digestion, and immune defense.
We want it to be modern, vibrant and appealing.
Bottle size: standard size supplement CLEAR bottle size, with white child resistant cap and the label panel dimensions are 3” x 7”. The label should be primarily white and green, with a touch of red; (see color palettes)/it can also ONLY be white and green. See samples attached.
We are only focused on the front of the bottle design, not on the back, but leave space for the supplement panel and other text on the back.
So the text for the front of the bottle is:
RT Halvorsen's
Meadow Crunch Chews™
Super Greens Blend for:
Energy, Digestion, and Immune Support*
60 Gummies | Dietary Supplement
Raspberry Flavor Gummies
Off to side of the label:
Non-GMO
Vegan Friendly
Plant-Based
Gelatin Free
Colors
Designer to choose colors to be used in the design.
Look and feel
Each slider illustrates characteristics of the customer's brand and the style your logo design should communicate.

```html
<!DOCTYPE html>
<html lang="en">
<head>
<meta charset="utf-8">
<title>Meadow Crunch Chews – Front Label</title>
<link rel="stylesheet" href="https://fonts.googleapis.com/css2?family=Albert+Sans:wght@500;600&family=Poppins:wght@400;500;600&family=Great+Vibes&display=swap">
<style>
  :root {
    --page-bg: #e4e4e4;
    --label-green-light: #2c7d3d;
    --label-green: #1d6630;
    --label-green-deep: #0c451b;
    --ink-white: #ffffff;
    --strip-white: #f7f7f5;
    --badge-line: #2d6b39;
    --box-text: #1f6a31;
  }
  * { margin: 0; padding: 0; box-sizing: border-box; }
  html, body {
    width: 1200px; height: 840px; overflow: hidden;
    background: var(--page-bg);
  }
  .canvas { position: relative; width: 1200px; height: 840px; }
  .label {
    position: absolute; left: 200px; top: 44px;
    width: 800px; height: 752px; overflow: hidden;
    background: linear-gradient(100deg, var(--label-green-light) 0%, var(--label-green) 45%, var(--label-green-deep) 100%);
    color: var(--ink-white);
  }
  .claims-strip {
    position: absolute; left: 18px; top: 0;
    width: 50px; height: 512px;
    background: var(--strip-white);
    border-radius: 0 0 25px 25px;
  }
  .claim {
    position: absolute; left: 0; width: 50px;
    display: flex; flex-direction: column; align-items: center; gap: 4px;
  }
  .claim-badge {
    width: 28px; height: 28px; border-radius: 50%;
    border: 1.5px solid var(--badge-line);
  }
  .claim-name {
    font: 500 6px/1 "Poppins", sans-serif; color: var(--badge-line);
    white-space: nowrap;
  }
  .brand-owner {
    position: absolute; right: 120px; top: 84px;
    font: 500 38px/1 "Poppins", sans-serif; letter-spacing: 2px;
    white-space: nowrap;
  }
  .product-name {
    position: absolute; right: 52px; top: 148px; text-align: center;
    font: 500 108px/0.98 "Albert Sans", sans-serif; letter-spacing: -2px;
    white-space: nowrap;
  }
  .product-form {
    position: absolute; left: 276px; top: 432px; width: 472px;
    display: flex; align-items: center; gap: 22px;
    font: 600 24px/1 "Poppins", sans-serif; letter-spacing: 7px;
  }
  .product-form::before, .product-form::after {
    content: ""; flex: 1; height: 2px; background: var(--ink-white);
  }
  .flavor-line {
    position: absolute; left: 288px; top: 500px;
    font: 400 36px/1 "Great Vibes", cursive; white-space: nowrap;
  }
  .benefits {
    position: absolute; left: 140px; top: 552px; width: 660px;
    display: flex; gap: 8px; list-style: none;
  }
  .benefit {
    background: var(--ink-white); color: var(--box-text);
    height: 98px; display: flex; align-items: center; justify-content: center;
    padding: 0 8px; white-space: nowrap;
    font: 500 34px/1 "Poppins", sans-serif; letter-spacing: -0.5px;
    border-radius: 4px;
  }
  .benefit-energy { width: 170px; }
  .benefit-digestion { width: 220px; }
  .benefit-immune { width: 254px; font-size: 28px; letter-spacing: -0.6px; border-radius: 4px 0 0 4px; }
  .net-contents {
    position: absolute; left: 244px; top: 700px;
    font: 400 27px/1 "Poppins", sans-serif; white-space: nowrap;
  }
  .net-contents strong { font-weight: 600; }
</style>
</head>
<body>
<div class="canvas">
  <section class="label">
    <aside class="claims-strip">
      <div class="claim" style="top:60px"><span class="claim-badge"></span></div>
      <div class="claim" style="top:184px"><span class="claim-badge"></span><span class="claim-name">Vegan Friendly</span></div>
      <div class="claim" style="top:302px"><span class="claim-badge"></span><span class="claim-name">Plant Based</span></div>
      <div class="claim" style="top:430px"><span class="claim-badge"></span></div>
    </aside>

    <p class="brand-owner">RT HALVORSEN'S</p>
    <h1 class="product-name">MEADOW<br>CRUNCH</h1>
    <p class="product-form">CHEWS</p>
    <p class="flavor-line">Raspberry Flavor Gummies Blend for:</p>

    <ul class="benefits">
      <li class="benefit benefit-energy">Energy</li>
      <li class="benefit benefit-digestion">Digestion</li>
      <li class="benefit benefit-immune">Immune Support</li>
    </ul>

    <p class="net-contents">DIETARY SUPPLEMENT | <strong>60 GUMMIES</strong></p>
  </section>
</div>
</body>
</html>
```